business card deign

Logo needs the following on it.
1. attached logo
2. Tagline - "If it keeps a drink cold or the party going...we do it!"
3. Name- Dalton Pikes, Founder and CPO
4. Address - 412 E. Carver Avenue, Ste 2207, Tampa, FL. 33917
5. Phone - 555.318.4726

```html
<!DOCTYPE html>
<html lang="en">
<head>
<meta charset="utf-8">
<title>HOPLEY business cards</title>
<link href="https://fonts.googleapis.com/css2?family=Arimo:wght@400;700&display=swap" rel="stylesheet">
<style>
  :root {
    --backdrop: #e6e6e4;
    --card: #262626;
    --card-edge: #1d1d1d;
    --ink: #f2f2f2;
    --ink-soft: #c9c9c9;
    --rule: #9a9a9a;
    --art-dark: #161616;
    --art-light: #4a4a4c;
  }
  * { box-sizing: border-box; margin: 0; padding: 0; }
  html, body {
    width: 1200px; height: 801px; overflow: hidden;
    background: var(--backdrop);
    font-family: "Arimo", Arial, sans-serif;
  }
  .sheet {
    width: 1200px; height: 801px;
    display: flex; align-items: center; justify-content: center; gap: 40px;
  }
  .card {
    position: relative;
    width: 540px; height: 308px;
    background: var(--card);
    border: 1px solid var(--card-edge);
    overflow: hidden;
    color: var(--ink);
  }

  /* Front: contact side */
  .logo-block {
    position: absolute; right: 40px; top: 26px;
    width: 180px; text-align: center;
  }
  .logo-art {
    display: block; width: 96px; height: 118px; margin: 0 auto 10px;
  }
  .wordmark {
    font-weight: 700; letter-spacing: 0.42em; color: var(--ink);
    white-space: nowrap;
  }
  .logo-block .wordmark { font-size: 24px; padding-left: 0.42em; }
  .person {
    position: absolute; left: 60px; top: 166px;
  }
  .person-name { font-size: 20px; font-weight: 700; line-height: 1.1; }
  .person-role { font-size: 15px; color: var(--ink-soft); line-height: 1.3; }
  .divider {
    position: absolute; left: 60px; right: 40px; top: 214px;
    height: 1px; background: var(--rule);
  }
  .address {
    position: absolute; left: 60px; top: 228px;
    font-style: normal;
    font-size: 14px; line-height: 1.45; color: var(--ink-soft);
  }
  .phone {
    position: absolute; right: 40px; top: 226px;
    display: flex; align-items: center; gap: 6px;
    font-size: 14px; color: var(--ink-soft);
  }
  .phone svg { width: 12px; height: 12px; }

  /* Back: brand side */
  .hero-art {
    position: absolute; right: 0; top: 0; width: 300px; height: 308px;
  }
  .back-wordmark {
    position: absolute; left: 34px; bottom: 52px;
    font-size: 40px; line-height: 1;
  }
  .tagline {
    position: absolute; left: 36px; bottom: 24px;
    font-size: 12px; color: var(--ink-soft); letter-spacing: 0.02em;
  }
</style>
</head>
<body>
<main class="sheet">

  <section class="card card-front">
    <div class="logo-block">
      <svg class="logo-art" role="img" aria-label="White kangaroo silhouette illustration" viewBox="0 0 96 118">
        <rect width="96" height="118" rx="6" fill="#d9d9d9"/>
      </svg>
      <div class="wordmark">HOPLEY</div>
    </div>

    <div class="person">
      <div class="person-name">Dalton Pikes</div>
      <div class="person-role">Founder and CPO</div>
    </div>
    <div class="divider"></div>
    <address class="address">
      412 E. Carver Avenue<br>
      Ste 2207, Tampa, FL. 33917
    </address>
    <div class="phone">
      <svg viewBox="0 0 24 24" aria-hidden="true"><path fill="currentColor" d="M6.6 10.8a15.1 15.1 0 0 0 6.6 6.6l2.2-2.2c.3-.3.7-.4 1-.2 1.1.4 2.3.6 3.6.6.6 0 1 .4 1 1V20c0 .6-.4 1-1 1A17 17 0 0 1 3 4c0-.6.4-1 1-1h3.5c.6 0 1 .4 1 1 0 1.3.2 2.5.6 3.6.1.3 0 .7-.2 1z"/></svg>
      555.318.4726
    </div>
  </section>

  <section class="card card-back">
    <svg class="hero-art" role="img" aria-label="Large embossed kangaroo silhouette illustration" viewBox="0 0 300 308" preserveAspectRatio="none">
      <defs>
        <linearGradient id="heroShade" x1="0" y1="0" x2="0" y2="1">
          <stop offset="0" stop-color="#161616"/>
          <stop offset="1" stop-color="#4a4a4c"/>
        </linearGradient>
      </defs>
      <rect width="300" height="308" fill="url(#heroShade)"/>
    </svg>
    <div class="wordmark back-wordmark">HOPLEY</div>
    <p class="tagline">If it keeps a drink cold or the party going...we do it!</p>
  </section>

</main>
</body>
</html>
```